4th Generation Family Business Needs a New Card Design!

We are a family owned 4th Generation company. We are based in the Sydney, Australia area and we are desperately in need of a more modern and classy card. We are monumental masons who design, supply & erect lasting memorials throughout cemeteries in Sydney. Our customers are normally in a period of grieving. I have attached logo files that will need to be implemented on the card. Company was established 1935. Australian Owned and Operated. Card needs to be designed to PIXO.com specification.

Target Market(s)

Our target market is based upon people that a grieving for family members that have passed away. We also deal with alot of companies that own and operate cemeteries.

Industry/Entity Type

Business

Contact Information for Business Card

Simon Harcourt, Operations Manager, 0417293086, simon@harcourtmemorials.com.au
Lewis Harcourt, Director, 0491630572, lewis@harcourtmemorials.com.au
Phone # 02 9561 3048
Website: www.harcourtmemorials.com.au
Address: Suite 17, 8 Palfrey Lane, West Carlow, Sydney NSW 2156

Font styles to use
Serif
Decorative
Script

Requirements
Must have
• Would like to see the logo nicely implemented with a modern design. Embossed lettering would be a nice additive.

```html
<!DOCTYPE html>
<html lang="en">
<head>
<meta charset="utf-8">
<title>Harcourt Memorials – Business Card</title>
<link rel="stylesheet" href="https://fonts.googleapis.com/css2?family=Arimo:wght@400&family=Cinzel:wght@400&display=swap">
<style>
  :root {
    --backdrop: #e9e6e1;
    --card-white: #ffffff;
    --panel-dark: #2a2828;
    --accent-gold: #f0c530;
    --ink-dark: #1f1d1d;
    --text-light: #ffffff;
  }
  * { box-sizing: border-box; margin: 0; padding: 0; }
  html, body { width: 1200px; height: 892px; overflow: hidden; }
  body {
    background: var(--backdrop);
    font-family: "Arimo", Arial, sans-serif;
    display: flex;
    flex-direction: column;
    align-items: center;
    justify-content: center;
    gap: 40px;
  }
  .card {
    width: 640px;
    height: 390px;
    background: var(--card-white);
    box-shadow: 0 6px 18px rgba(0,0,0,0.18);
    display: flex;
    position: relative;
    overflow: hidden;
  }
  .card--front { align-items: center; justify-content: center; }
  .brand-name {
    font-family: "Cinzel", Georgia, serif;
    font-weight: 400;
    color: var(--ink-dark);
    font-size: 40px;
    letter-spacing: 1px;
    text-align: center;
    line-height: 1.15;
    display: flex;
    align-items: center;
    gap: 16px;
  }
  .brand-mark {
    width: 26px; height: 26px;
    background: var(--accent-gold);
    flex: none;
  }
  .contact-panel {
    width: 360px;
    height: 100%;
    background: var(--panel-dark);
    border-right: 7px solid var(--accent-gold);
    color: var(--text-light);
    padding: 46px 26px 0 30px;
  }
  .people { display: flex; align-items: flex-start; gap: 12px; margin-bottom: 40px; }
  .person-name { font-size: 21px; line-height: 1.05; white-space: nowrap; }
  .person-role { font-size: 14px; color: var(--accent-gold); white-space: nowrap; }
  .people-divider { width: 2px; height: 36px; background: var(--text-light); margin-top: 4px; }
  .contact-list { list-style: none; font-size: 14px; line-height: 1.3; }
  .contact-list li { display: flex; gap: 10px; margin-bottom: 4px; }
  .contact-icon {
    width: 18px; height: 18px; flex: none;
    background: var(--accent-gold);
    border-radius: 3px;
    margin-top: 1px;
  }
  .contact-icon svg { width: 18px; height: 18px; display: block; }
  .card-back-logo {
    flex: 1;
    display: flex; align-items: center; justify-content: center;
  }
  .card-back-logo .brand-name { font-size: 30px; flex-direction: column; gap: 10px; }
</style>
</head>
<body>

<section class="card card--front" aria-label="Card front">
  <div class="brand-name"><span class="brand-mark"></span>Harcourt Memorials</div>
</section>

<section class="card card--back" aria-label="Card back">
  <div class="contact-panel">
    <div class="people">
      <div class="person">
        <p class="person-name">Simon Harcourt</p>
        <p class="person-role">Operations Manager</p>
      </div>
      <span class="people-divider"></span>
      <div class="person">
        <p class="person-name">Lewis Harcourt</p>
        <p class="person-role">Director</p>
      </div>
    </div>
    <ul class="contact-list">
      <li><span class="contact-icon"><svg viewBox="0 0 18 18"><rect x="6" y="3" width="6" height="12" rx="1" fill="none" stroke="#2a2828" stroke-width="1.4"/></svg></span>0417293086 / 0491630572</li>
      <li><span class="contact-icon"><svg viewBox="0 0 18 18"><path d="M5 4 L7.5 4 L8.5 7 L7 8 Q8 10.5 10 11 L11 9.5 L14 10.5 L14 13 Q8 14 5 7 Z" fill="#2a2828"/></svg></span>02 9561 3048</li>
      <li><span class="contact-icon"><svg viewBox="0 0 18 18"><rect x="3.5" y="5" width="11" height="8" fill="none" stroke="#2a2828" stroke-width="1.3"/><path d="M3.5 5 L9 9.5 L14.5 5" fill="none" stroke="#2a2828" stroke-width="1.3"/></svg></span><span>simon@harcourtmemorials.com.au<br>lewis@harcourtmemorials.com.au</span></li>
      <li><span class="contact-icon"><svg viewBox="0 0 18 18"><circle cx="9" cy="9" r="5" fill="none" stroke="#2a2828" stroke-width="1.3"/><path d="M4 9 H14 M9 4 V14" stroke="#2a2828" stroke-width="1"/></svg></span>www.harcourtmemorials.com.au</li>
      <li><span class="contact-icon"><svg viewBox="0 0 18 18"><path d="M9 15 L5.2 9 A4.3 4.3 0 1 1 12.8 9 Z" fill="#2a2828"/><circle cx="9" cy="7" r="1.6" fill="#f0c530"/></svg></span><span>Suite 17, 8 Palfrey Lane, West Carlow,<br>Sydney NSW 2156</span></li>
    </ul>
  </div>
  <div class="card-back-logo">
    <div class="brand-name"><span class="brand-mark"></span>Harcourt Memorials</div>
  </div>
</section>

</body>
</html>
```